Elegant and modern Wedding Photography brochure

My existing brochure (attached) needs a major facelift. This is one of the main selling tools - it gets emailed to my clients when they make an equiry on what packages i offer and it is printed out and walked through at our first meeting. This brochure is as critical as my website - it needs to sing!

I'm looking for an eye-catching design that says:
Elegant
Modern
Clean
Crisp
Not cutesy or lovey-dovey thanks - we are more sophisticated and professional than that.

Update images to some of the latest weddings I've shot also. Let me know files and resolution you need. I've enabled right-click to download images on my site for a limited time. Please note that I retain copyright and will pursue any breeches.

Http://www.sarahkelbrin.com/Melbourne-wedding-photography
Updates

Thanks for all of your designs! Will take a few days to decide.

Target Market(s)

Australian Women aged 24-44

Industry/Entity Type

Wedding

Font styles to use
Other font styles liked:
• Century Gothic

Requirements
Must have
• Easy to print - does not have to be 6 A4 pages like the existing brochure
Nice to have
• Some full page images - The photos are supposed to be the hero here :-)
Should not have
• Not cutesy or lovey-dovey thanks - we are more sophisticated and professional than that.

No black backgrounds, I prefer a white thanks

No images in organic shaped boxes (like the rectangles in the logo - no thanks).
Keep the lines straight and sharp

```html
<!DOCTYPE html>
<html lang="en">
<head>
<meta charset="utf-8">
<title>Sarah Kelbrin Wedding Photography</title>
<link href="https://fonts.googleapis.com/css2?family=Questrial&display=swap" rel="stylesheet">
<style>
  :root {
    --plum: #92278f;
    --slate: #939598;
    --ink: #1a1a1a;
    --paper: #ffffff;
  }
  * { margin: 0; padding: 0; box-sizing: border-box; }
  html, body { width: 853px; height: 1200px; overflow: hidden; background: var(--paper); }
  .brochure {
    position: relative;
    width: 853px;
    height: 1200px;
    font-family: "Questrial", "Century Gothic", sans-serif;
    color: var(--ink);
  }
  .headline {
    position: absolute;
    left: 58px;
    top: 52px;
    width: 660px;
    font-weight: 400;
    font-size: 41px;
    line-height: 48px;
    color: var(--plum);
  }
  .intro {
    position: absolute;
    left: 58px;
    top: 187px;
    width: 665px;
    font-size: 16px;
    line-height: 20px;
  }
  .intro p { margin-bottom: 20px; }
  .photo {
    position: absolute;
    border: 8px solid var(--plum);
    background-clip: padding-box;
  }
  .photo-dance {
    left: 78px; top: 428px; width: 310px; height: 232px;
    background-image: linear-gradient(135deg, #c9b79a 0%, #8a9aa0 45%, #b98f6e 75%, #5f5a52 100%);
  }
  .photo-embrace {
    left: 478px; top: 428px; width: 290px; height: 220px;
    background-image: linear-gradient(120deg, #4d5557 0%, #7f8a86 40%, #c8bfb1 65%, #3b3f40 100%);
  }
  .photo-portrait {
    left: 280px; top: 590px; width: 306px; height: 244px;
    border-color: var(--slate);
    background-image: linear-gradient(110deg, #3b6d4a 0%, #2c2c30 35%, #c9a98a 60%, #d0a64a 85%, #8f7b5e 100%);
  }
  .brand {
    position: absolute;
    left: 0; top: 896px;
    width: 853px;
    display: flex;
    justify-content: center;
    align-items: center;
    gap: 12px;
    font-size: 31px;
    color: var(--plum);
  }
  .brand-mark {
    width: 34px; height: 34px;
    border: 3px solid var(--plum);
  }
  .contact {
    position: absolute;
    left: 58px; top: 972px;
    width: 746px; height: 191px;
    background: var(--slate);
    color: var(--paper);
    text-align: center;
    font-size: 21px;
    line-height: 28px;
    padding-top: 36px;
    font-style: normal;
  }
</style>
</head>
<body>
<main class="brochure">
  <h1 class="headline">How do you want to remember your special day?</h1>

  <section class="intro">
    <p>Elegant, stunning, fuss-free photography that doesn’t cost the earth will capture those memories for a lifetime!</p>
    <p>Wedding photography packages start from $1650 and are fully inclusive of fun-filled creative &amp; journalistic coverage, digital negatives and professionally edited album.</p>
    <p>Contact Sarah today to arrange an informal catch-up, discuss your requirements and find out more about the early booking bonus!</p>
  </section>

  <div class="photo photo-dance" role="img" aria-label="Couple dancing hand in hand in front of a colourful street-art mural"></div>
  <div class="photo photo-embrace" role="img" aria-label="Couple embracing against a graffiti-covered laneway wall"></div>
  <div class="photo photo-portrait" role="img" aria-label="Portrait of the couple standing together before bright graffiti"></div>

  <div class="brand">
    <span class="brand-mark"></span>
    <span class="brand-name">Sarah Kelbrin</span>
  </div>

  <address class="contact">
    www.sarahkelbrin.com<br>
    Mobile: 0400 555 018<br>
    Email: sarah@sarahkelbrin.com<br>
    Banksia Lane, Seddon, VIC, 3011
  </address>
</main>
</body>
</html>
```